Business card design for my company.
I would like the card's background colour to be black. You can also see our web site to get an idea of our brand. https://www.tmwhomecrafting.com.au/
- Name
- Email

```html
<!DOCTYPE html>
<html lang="en">
<head>
<meta charset="utf-8">
<title>TMW Home Crafting – Business Card</title>
<link rel="stylesheet" href="https://fonts.googleapis.com/css2?family=Barlow:wght@600;700;800&family=Montserrat:wght@400&display=swap">
<style>
  :root {
    --stage: #3a3a3a;
    --card-black: #0b0b0b;
    --facet: #151515;
    --facet-dark: #050505;
    --brand-green: #1aa34a;
    --white: #ffffff;
    --silver: #c9c9c9;
    --gold: #d4a62a;
    --badge-dark: #2a2a2a;
    --badge-ring: #9a9a9a;
    --badge-blue: #1f4fa0;
    --orange: #f2a11c;
  }
  * { margin: 0; padding: 0; box-sizing: border-box; }
  html, body { width: 1200px; height: 886px; overflow: hidden; }
  body { background: var(--stage); position: relative; }

  .card {
    position: absolute;
    width: 560px;
    height: 320px;
    background: var(--card-black);
    overflow: hidden;
    box-shadow: 0 18px 40px rgba(0,0,0,0.45);
  }
  .card-front { left: 80px; top: 100px; }
  .card-back { left: 560px; top: 466px; }
  .card-art { position: absolute; inset: 0; width: 100%; height: 100%; }

  .brand {
    position: absolute;
    display: flex;
    align-items: center;
    gap: 14px;
  }
  .brand-square {
    width: 22px;
    height: 22px;
    background: var(--brand-green);
    flex: none;
  }
  .brand-name {
    font-family: "Barlow", sans-serif;
    font-weight: 700;
    color: var(--white);
    line-height: 1;
    text-transform: uppercase;
  }
  .brand-name .brand-initials { display: block; font-size: 68px; letter-spacing: 2px; }
  .brand-name .brand-words { display: block; font-size: 17px; letter-spacing: 4px; margin-top: 6px; }

  .card-front .brand { left: 175px; top: 92px; }
  .card-back .brand { left: 60px; top: 82px; }

  .contact {
    position: absolute;
    left: 60px;
    top: 222px;
    color: var(--white);
  }
  .contact-name {
    font-family: "Barlow", sans-serif;
    font-weight: 800;
    font-size: 30px;
    letter-spacing: 0.5px;
    text-transform: uppercase;
    line-height: 1;
    margin-bottom: 10px;
  }
  .contact-line {
    font-family: "Montserrat", sans-serif;
    font-weight: 400;
    font-size: 15px;
    line-height: 1.35;
  }
  .accent-bar {
    position: absolute;
    left: 0;
    top: 222px;
    width: 24px;
    height: 98px;
    background: var(--brand-green);
  }
</style>
</head>
<body>

  <section class="card card-front" aria-label="Business card front">
    <svg class="card-art" viewBox="0 0 560 320" aria-hidden="true">
      <polygon points="0,0 560,0 560,140 330,90" fill="var(--facet)"/>
      <polygon points="0,150 260,230 0,280" fill="var(--facet-dark)"/>
      <polygon points="0,282 560,176 560,222 0,320" fill="var(--brand-green)"/>
      <polygon points="0,320 560,222 560,320" fill="var(--card-black)"/>
    </svg>
    <div class="brand">
      <span class="brand-square"></span>
      <p class="brand-name"><span class="brand-initials">TMW</span><span class="brand-words">Home Crafting</span></p>
    </div>
  </section>

  <section class="card card-back" aria-label="Business card back">
    <svg class="card-art" viewBox="0 0 560 320" aria-hidden="true">
      <polygon points="0,0 560,0 560,60 260,40" fill="var(--facet)"/>
      <polygon points="0,200 560,130 560,320 0,320" fill="var(--facet-dark)"/>
      <g class="award-badges">
        <circle cx="345" cy="95" r="26" fill="var(--silver)"/>
        <circle cx="370" cy="152" r="26" fill="var(--silver)"/>
        <circle cx="395" cy="209" r="26" fill="var(--white)" stroke="var(--badge-blue)" stroke-width="5"/>
        <circle cx="402" cy="68" r="26" fill="var(--gold)"/>
        <circle cx="427" cy="125" r="26" fill="var(--gold)"/>
        <circle cx="452" cy="182" r="26" fill="var(--badge-dark)" stroke="var(--badge-ring)" stroke-width="3"/>
        <circle cx="459" cy="41" r="26" fill="var(--badge-dark)" stroke="var(--badge-ring)" stroke-width="3"/>
        <circle cx="484" cy="98" r="26" fill="var(--badge-dark)" stroke="var(--badge-ring)" stroke-width="3"/>
        <circle cx="509" cy="155" r="26" fill="var(--orange)"/>
      </g>
    </svg>
    <div class="brand">
      <span class="brand-square"></span>
      <p class="brand-name"><span class="brand-initials">TMW</span><span class="brand-words">Home Crafting</span></p>
    </div>
    <span class="accent-bar"></span>
    <div class="contact">
      <p class="contact-name">Your Name Here</p>
      <p class="contact-line">youremail@tmwhomecrafting.com.au</p>
      <p class="contact-line">www.tmwhomecrafting.com.au</p>
    </div>
  </section>

</body>
</html>
```